Need App for Impact Related Events

My app is to help with internal events. When you enter the prompted event code the next screen shows you everyone currently at the event. It will give you the ability to Start a conversation with someone you met at that event, or signal it is your turn to send a message. The next screen is a message thread with that person. I am looking for a design that incorporates the colors and ‘feel good’ emotion of our logo. I have pieced together a pretty good interpretation of what I’m looking for in the attached mockup by slicing and dicing designs. I also attached our logo mascot.Screens (see attached mockups)

Note 1: I do not like the picture on the screen used in screen one because it makes it seem like a dating app. I attached an alternative photo that can be used or present different ideas.

Note 2: On the login/signup screen (screen 2) I need an additional first and last name for login, you can try to fit this on one login screen or present a two step signup screen where that is presented in the second screen.

READ MOCKUP GUIDELINES UNDER Must Haves

Target Market(s)

People attending internal social impact events

Industry/Entity Type

Charity

Font styles to use
Sans Serif

Colors
86cfc6

Requirements
Must have
• Follow the screen mockups attached to project
• PLEASE READ
• I have provided a relatively close design of what I’m looking for in the mockups. Some screens need to be followed more closely to my design mockup than other. I have listed a guide below how how closely you should follow my mockup design exactly. Overall I would like to see some ideas of incorporating a few accent colors so it doesn’t appear SO Blue. I also attached some app inspiration designs I found from around the web
• Screen Mockup Guideline Follow %
• Screen 1: 65% - mostly on target, would like to see ways to make it not SO Blue and possibly creative places to add some explainer text describing the app
• Screen 2: 50% - general design idea is here, but more open
• Screen 3: 35% - a lot more room for design influence
• Screen 4: 70% - mostly on target, a little room for design influence/color scheme ideas
• Screen 5-6: 25% - a lot of room for design change/ideas/influence
• Screen 7-8: 80% - already very close to what I need, maybe open to slight sizing and color scheme ideas
• Screen 9: 15% - the most open for influence, only the general functionality of the screen is communicated here
Nice to have
• Please Read Mockup Guideline above. In large part I am looking for something to use some nice accent colors so it is not overwhelmingly blue and bring the whole design into a seamless style.
Should not have

```html
<!DOCTYPE html>
<html lang="en">
<head>
<meta charset="utf-8">
<title>Events</title>
<link rel="stylesheet" href="https://fonts.googleapis.com/css2?family=Nunito+Sans:wght@400;600;700;800&display=swap">
<style>
  :root {
    --teal: #16c5c8;
    --ink: #1f2230;
    --muted: #8a8d96;
    --line: #e7e8ec;
    --bg: #ffffff;
    --card-shadow: rgba(20, 30, 50, 0.16);
    --pink-1: #ff4f8e;
    --pink-2: #f7a1bf;
    --avatar: #b9b4b0;
  }
  * { box-sizing: border-box; margin: 0; padding: 0; }
  html, body { width: 675px; height: 1200px; overflow: hidden; background: var(--bg); }
  body { font-family: "Nunito Sans", sans-serif; color: var(--ink); position: relative; }

  .page-title { position: absolute; left: 30px; top: 34px; font-size: 50px; font-weight: 800; letter-spacing: 0.5px; }
  .profile-avatar { position: absolute; left: 581px; top: 34px; width: 64px; height: 64px; border-radius: 50%;
    background: linear-gradient(135deg, #d8d6d3, #6f6b68); }

  .search-field { position: absolute; left: 56px; top: 141px; width: 563px; height: 75px;
    border: 2px solid var(--line); border-radius: 8px; display: flex; align-items: center;
    padding: 0 26px; font-size: 26px; color: var(--muted); justify-content: space-between; }

  .tabs { position: absolute; left: 195px; top: 240px; display: flex; align-items: center; }
  .tab { height: 73px; display: flex; align-items: center; font-size: 25px; font-weight: 800; letter-spacing: 2.5px; }
  .tab--active { background: var(--teal); color: #fff; border-radius: 4px; padding: 0 24px; width: 159px; justify-content: center; }
  .tab--idle { margin-left: 39px; color: var(--ink); }

  .event-card { position: absolute; left: 30px; top: 338px; width: 615px; height: 468px;
    border-radius: 8px; background: #fff; box-shadow: 0 3px 12px var(--card-shadow); overflow: hidden; }
  .event-cover { height: 300px; background: radial-gradient(circle at 60% 30%, var(--pink-1), #e83c7c 45%, var(--pink-2) 100%); }
  .event-name { position: absolute; left: 17px; top: 320px; font-size: 37px; font-weight: 700; }
  .event-date { position: absolute; left: 17px; top: 382px; font-size: 25px; font-weight: 600; color: #4a4d57; letter-spacing: 0.5px; }
  .guests { position: absolute; right: 21px; top: 388px; display: flex; gap: 11px; }
  .guest { width: 64px; height: 64px; border-radius: 50%; background: var(--avatar); }
  .guest:nth-child(2) { background: #c9a08a; }
  .guest:nth-child(3) { background: #a4867a; }
  .guest--more { background: var(--teal); color: #fff; font-size: 20px; font-weight: 800;
    display: flex; align-items: center; justify-content: center; }

  .tab-bar { position: absolute; left: 0; top: 1080px; width: 675px; height: 120px; }
</style>
</head>
<body>
  <h1 class="page-title">Events</h1>
  <div class="profile-avatar" role="img" aria-label="Profile photo of the signed-in user"></div>

  <div class="search-field">
    <span>Search for the events</span>
    <svg width="32" height="32" viewBox="0 0 32 32" fill="none" stroke="var(--teal)" stroke-width="3" stroke-linecap="round">
      <circle cx="14" cy="14" r="10"/><line x1="21.5" y1="21.5" x2="28" y2="28"/>
    </svg>
  </div>

  <nav class="tabs">
    <div class="tab tab--active">INVITES</div>
    <div class="tab tab--idle">YOUR</div>
  </nav>

  <article class="event-card">
    <div class="event-cover" role="img" aria-label="Photo of pink party balloons"></div>
    <h2 class="event-name">Maren's Party</h2>
    <p class="event-date">22 - Sep - 2018</p>
    <div class="guests">
      <div class="guest" role="img" aria-label="Guest photo"></div>
      <div class="guest" role="img" aria-label="Guest photo"></div>
      <div class="guest" role="img" aria-label="Guest photo"></div>
      <div class="guest guest--more">9+</div>
    </div>
  </article>

  <svg class="tab-bar" viewBox="0 0 675 120" fill="none" stroke="var(--teal)" stroke-width="4" stroke-linecap="round" stroke-linejoin="round">
    <circle cx="67" cy="26" r="8" fill="var(--teal)" stroke="none"/>
    <rect x="44" y="51" width="46" height="42" rx="5"/>
    <line x1="44" y1="63" x2="90" y2="63"/>
    <line x1="56" y1="45" x2="56" y2="55"/><line x1="78" y1="45" x2="78" y2="55"/>
    <path d="M204 55 a18 17 0 1 1 -9 31 l-9 4 l3 -9 a18 17 0 0 1 15 -26 z"/>
    <circle cx="338" cy="54" r="51" fill="var(--teal)" stroke="none"/>
    <line x1="338" y1="36" x2="338" y2="72" stroke="#fff"/>
    <line x1="320" y1="54" x2="356" y2="54" stroke="#fff"/>
    <path d="M460 84 h28 l-4 -6 v-12 a10 10 0 0 0 -20 0 v12 z"/>
    <line x1="474" y1="50" x2="474" y2="55"/>
    <path d="M469 89 a5 5 0 0 0 10 0"/>
    <line x1="584" y1="61" x2="628" y2="61"/><line x1="584" y1="80" x2="628" y2="80"/>
    <circle cx="614" cy="61" r="6" fill="#fff"/><circle cx="598" cy="80" r="6" fill="#fff"/>
  </svg>
</body>
</html>
```